Website Design for WestaKolory.pl – Luxury Wedding Car Rental with Chauffeur

We are looking for a talented designer to create a modern, elegant, and fully responsive website for our new brand – WestyKolory.pl. We are a premium car rental platform in Poland, offering luxury and exotic vehicles exclusively for weddings. All cars come with a professional chauffeur, ensuring a high-end, stress-free, and stylish experience.
Website Purpose:
The website should present our offering in a luxurious, clear, and inspiring way. It must build trust, highlight the prestige of our brand, and encourage inquiries. Our target audience includes engaged couples, wedding planners, and clients seeking a truly exceptional vehicle for their special day.
Design Requirements:
Style: modern, elegant, minimalist
Color palette: white, black, gold, optionally silver – refined and luxurious
Typography: clean, modern, high-end
Layout: clear, intuitive, with large car images and well-defined sections
Fully responsive (desktop, tablet, mobile)
Bilingual layout (Polish/English) must be considered
Pages to Design:
Homepage
About Us
Fleet Overview
Individual Car Pages
Services (Weddings, Photo Shoots, Film Rentals)
Why Us / Unique Selling Points
Contact
FAQ
Inspiration:
Luxury automotive brands (e.g. Varnel-Hoske, Corvash, Elbrin Tusko)
High-end wedding websites
Minimalist layouts with large visuals and elegant typography
Additional Notes:
The design should evoke the emotions of a wedding day – elegance, uniqueness, style, and class. Please avoid flashy colors, excessive graphic effects, or overly decorative elements. Subtlety, prestige, and sophistication are key.

```html
<!DOCTYPE html>
<html lang="en">
<head>
<meta charset="utf-8">
<title>WestaKolory.pl – Luxury Wedding Cars</title>
<link rel="stylesheet" href="https://fonts.googleapis.com/css2?family=Outfit:ital,wght@0,300;0,400;0,500;0,600;0,700;1,300;1,400&display=swap">
<style>
:root{
  --ink:#2b2b2e;
  --muted:#6b6b70;
  --gold:#d9b44a;
  --gold-soft:#f7d774;
  --gold-light:#fbe49a;
  --navy:#171c2b;
  --navy-card:#232938;
  --navy-line:#3a4152;
  --white:#ffffff;
}
*{box-sizing:border-box;margin:0;padding:0}
html,body{width:1200px;height:3084px;overflow:hidden}
body{font-family:"Outfit",sans-serif;color:var(--ink);background:var(--white)}
.container{width:695px;margin:0 auto;position:relative}
.gold{color:var(--gold)}
.btn{display:inline-block;font-family:"Outfit",sans-serif;font-weight:500;border-radius:4px;text-decoration:none;color:var(--ink)}
.btn-gold{background:var(--gold-soft);padding:0 26px;height:35px;line-height:35px;font-size:12px}
.btn-outline{background:var(--white);border:2px solid var(--gold-soft);height:28px;line-height:24px;padding:0 20px;font-size:9.5px}

/* Hero */
.hero{height:650px;position:relative;text-align:center;overflow:hidden}
.hero-photo{position:absolute;inset:0;background:
  radial-gradient(ellipse 300px 140px at 560px 450px,rgba(40,40,42,.75),rgba(40,40,42,0) 100%),
  linear-gradient(180deg,#f6f6f4 0%,#eeeeec 38%,#c9ccc4 52%,#6f7a62 66%,#8b8b86 82%,#a3a3a0 100%)}
.hero-content{position:relative;padding-top:22px}
.logo{display:inline-flex;align-items:center;gap:8px;font-weight:500;font-size:20px;color:var(--gold)}
.logo-dot{width:30px;height:30px;border:2px solid var(--gold);border-radius:50%}
.hero h1{font-size:47px;font-weight:600;line-height:52px;margin-top:14px;letter-spacing:-.3px}
.hero p{font-size:15.5px;font-weight:300;line-height:20px;margin:16px auto 0;width:640px}
.hero .btn{margin-top:20px}

/* About */
.about{height:428px;background:linear-gradient(180deg,#fbfbfa,#efeeea);text-align:center;padding-top:57px}
.section-title{font-size:31px;font-weight:600;letter-spacing:-.2px}
.about .lead{font-size:11.5px;font-weight:300;line-height:19px;width:570px;margin:14px auto 0}
.features{display:flex;gap:20px;margin-top:42px}
.feature{width:218px;height:168px;background:var(--white);border-radius:8px;box-shadow:0 2px 10px rgba(0,0,0,.08);padding:20px 18px 0}
.feature-icon{width:39px;height:39px;border-radius:50%;background:var(--gold-soft);margin:0 auto;display:flex;align-items:center;justify-content:center}
.feature h3{font-size:12.5px;font-weight:500;margin-top:14px}
.feature p{font-size:9.5px;font-weight:300;color:var(--muted);line-height:15px;margin-top:12px}

/* Fleet */
.fleet{height:590px;background:var(--navy);color:var(--white);text-align:center;padding-top:60px}
.fleet .sub{font-size:12.5px;font-weight:300;margin-top:10px;color:#d7d9de}
.cars{display:flex;gap:20px;margin-top:40px;text-align:left}
.car-card{width:218px;height:313px;background:var(--navy-card);border:1px solid var(--navy-line);border-radius:4px;padding:20px}
.car-photo{height:120px;border-radius:4px}
.car-card h3{font-size:15.5px;font-weight:600;margin-top:18px;line-height:20px}
.car-card .desc{font-size:10px;font-weight:300;color:#c8cbd2;line-height:15px;margin-top:6px}
.car-card ul{list-style:none;margin-top:10px}
.car-card li{font-size:9px;color:var(--gold-soft);line-height:18px;padding-left:11px;position:relative}
.car-card li::before{content:"";position:absolute;left:0;top:7px;width:4px;height:4px;border-radius:50%;background:var(--gold-soft)}
.fleet .btn{margin-top:31px}

/* Details */
.details{height:502px;background:linear-gradient(180deg,#efeeea,#fbfbfa);padding-top:50px}
.details .section-title{text-align:center}
.details-row{display:flex;justify-content:space-between;margin-top:50px}
.points{width:330px;list-style:none;padding-top:8px}
.points li{display:flex;gap:10px;margin-bottom:23px}
.points h4{font-size:13px;font-weight:500;line-height:17px}
.points p{font-size:9.5px;font-weight:300;color:var(--muted);line-height:16px;margin-top:5px}
.details-photo-wrap{position:relative;width:314px;height:314px}
.details-glow{position:absolute;left:-44px;top:8px;width:70px;height:70px;border-radius:50%;background:var(--gold-light);opacity:.5}
.details-photo{position:relative;width:314px;height:314px;border-radius:10px;background:linear-gradient(135deg,#9a8f7e 0%,#c4b49e 40%,#e9e6e2 65%,#8a7d70 100%)}

/* Testimonials */
.reviews{height:345px;background:var(--navy);color:var(--white);text-align:center;padding-top:60px}
.quotes{display:flex;gap:20px;margin-top:40px}
.quote{width:218px;height:156px;background:var(--navy-card);border:1px solid var(--navy-line);border-radius:4px;padding:20px 22px 0}
.stars{display:flex;justify-content:center}
.quote blockquote{font-size:10.5px;font-style:italic;font-weight:300;line-height:19px;color:#d7d9de;margin-top:13px}
.quote cite{display:block;font-style:normal;font-size:10px;color:var(--gold-soft);margin-top:11px}

/* CTA */
.cta{height:281px;position:relative;text-align:center;color:var(--white);overflow:hidden}
.cta-photo{position:absolute;inset:0;background:linear-gradient(90deg,#6b6a55 0%,#4e4f47 30%,#40443f 60%,#2f332f 100%)}
.cta-photo::after{content:"";position:absolute;inset:0;background:rgba(20,22,30,.35)}
.cta-content{position:relative;padding-top:62px;padding-left:130px}
.cta h2{font-size:31px;font-weight:600}
.cta p{font-size:12px;font-weight:300;margin-top:12px;margin-left:-130px}
.cta .btn{margin-top:20px}
.cta-rule{display:flex;align-items:center;justify-content:center;gap:8px;margin-top:25px}
.cta-rule span{width:90px;height:1px;background:var(--gold-soft);opacity:.8}
.cta-rule i{width:5px;height:5px;border-radius:50%;background:var(--gold-soft)}

/* Footer */
.footer{height:288px;background:var(--navy);color:var(--white);padding-top:48px}
.footer-top{display:flex}
.footer-brand{width:357px}
.footer-brand .logo{font-size:22px}
.footer-brand p{font-size:10px;font-weight:300;line-height:13px;color:#c8cbd2;margin-top:26px;width:245px}
.socials{display:flex;gap:12px;margin-top:20px}
.socials span{width:14px;height:14px;border:1.5px solid var(--gold-soft);border-radius:50%}
.footer-col{width:180px}
.footer-col h5{font-size:11px;font-weight:500;color:var(--gold-soft)}
.footer-col ul{list-style:none;margin-top:12px}
.footer-col li{font-size:9.5px;font-weight:300;color:#c8cbd2;line-height:20px;display:flex;align-items:center;gap:8px}
.footer-bottom{border-top:1px solid var(--navy-line);margin-top:30px;padding-top:22px;display:flex;justify-content:space-between;font-size:8.5px;font-weight:300;color:#b3b6bd}
</style>
</head>
<body>

<header class="hero">
  <div class="hero-photo" role="img" aria-label="Bride and groom leaning on a classic black car in a paved courtyard"></div>
  <div class="hero-content">
    <div class="logo"><span>WestaKolory.pl</span><span class="logo-dot"></span></div>
    <h1>Ani Exceptional Car<br><span class="gold">for Your Exceptional Day</span></h1>
    <p>Luxury wedding cars with professional chauffeurs. Experience timeless elegance, unmatched comfort, and flawless service on the most important day of your life.</p>
    <a class="btn btn-gold" href="#fleet">View Our Fleet</a>
  </div>
</header>

<section class="about">
  <div class="container">
    <h2 class="section-title">Where Luxury Meets <span class="gold">Love</span></h2>
    <p class="lead">WestaKolory.pl offers a handpicked selection of luxury vehicles exclusively for weddings. Each car comes with a professionally dressed chauffeur, ensuring a seamless, stylish, and stress-free experience. Whether for the ceremony, a photo shoot, or a grand arrival — we deliver elegance that turns heads.</p>
    <div class="features">
      <div class="feature">
        <div class="feature-icon"><svg width="18" height="18" viewBox="0 0 24 24" fill="none" stroke="#2b2b2e" stroke-width="2" stroke-linecap="round" stroke-linejoin="round"><path d="M3 16V12l2-4h12l3 4h1v4H3z"/><circle cx="7.5" cy="16.5" r="1.8"/><circle cx="16.5" cy="16.5" r="1.8"/></svg></div>
        <h3>Luxury Interiors</h3>
        <p>Premium leather seats, champagne setup, and elegant decorations to make every moment special.</p>
      </div>
      <div class="feature">
        <div class="feature-icon"><svg width="18" height="18" viewBox="0 0 24 24" fill="none" stroke="#2b2b2e" stroke-width="2" stroke-linecap="round"><circle cx="12" cy="8" r="4"/><path d="M5 21c0-4 3-6 7-6s7 2 7 6"/></svg></div>
        <h3>Professional Service</h3>
        <p>Impeccably dressed chauffeurs with white gloves, ensuring punctual and courteous service.</p>
      </div>
      <div class="feature">
        <div class="feature-icon"><svg width="18" height="18" viewBox="0 0 24 24" fill="none" stroke="#2b2b2e" stroke-width="2" stroke-linejoin="round"><path d="M12 20s-8-5-8-11a4.5 4.5 0 0 1 8-2.5A4.5 4.5 0 0 1 20 9c0 6-8 11-8 11z"/></svg></div>
        <h3>Unforgettable Moments</h3>
        <p>Creating magical memories for couples with elegant arrivals and perfect photo opportunities.</p>
      </div>
    </div>
  </div>
</section>

<section class="fleet" id="fleet">
  <div class="container">
    <h2 class="section-title">Meet Our Signature Wedding Cars</h2>
    <p class="sub">Curated for elegance. Maintained to perfection.</p>
    <div class="cars">
      <article class="car-card">
        <div class="car-photo" role="img" aria-label="White luxury sedan driving across a bridge" style="background:linear-gradient(180deg,#c9cdd2,#8c9198 60%,#5d6168)"></div>
        <h3>Corvash Aurel Grand</h3>
        <p class="desc">The epitome of British luxury and craftsmanship</p>
        <ul><li>Handcrafted interior</li><li>Whisper-quiet ride</li><li>Premium leather</li></ul>
      </article>
      <article class="car-card">
        <div class="car-photo" role="img" aria-label="Gold luxury coupe in a grey studio" style="background:linear-gradient(180deg,#9a9896,#7d7560 55%,#b9953f 75%,#6e6b66)"></div>
        <h3>Varnel-Hoske Serene</h3>
        <p class="desc">Unparalleled elegance and sophistication</p>
        <ul><li>Starlight headliner</li><li>Magic carpet ride</li><li>Bespoke details</li></ul>
      </article>
      <article class="car-card">
        <div class="car-photo" role="img" aria-label="Two-tone black limousine by a modern house at dusk" style="background:linear-gradient(180deg,#4f7fae,#9bb3c9 45%,#6a4a3a 70%,#3a3533)"></div>
        <h3>Delmont-Arvik Lumen Tour</h3>
        <p class="desc">German engineering meets ultimate comfort</p>
        <ul><li>Executive seating</li><li>Champagne cooler</li><li>Ambient lighting</li></ul>
      </article>
    </div>
    <a class="btn btn-outline" href="#fleet">Explore the Full Fleet</a>
  </div>
</section>

<section class="details">
  <div class="container">
    <h2 class="section-title">Because Every Detail <span class="gold">Matters</span></h2>
    <div class="details-row">
      <ul class="points">
        <li><svg width="15" height="15" viewBox="0 0 24 24" fill="none" stroke="#f7d774" stroke-width="2" stroke-linecap="round"><circle cx="12" cy="12" r="10"/><path d="M8 12l3 3 5-6"/></svg><div><h4>Premium vehicles with full decorative setup</h4><p>Every car is meticulously prepared with elegant decorations and luxury amenities</p></div></li>
        <li><svg width="15" height="15" viewBox="0 0 24 24" fill="none" stroke="#f7d774" stroke-width="2" stroke-linecap="round"><circle cx="12" cy="12" r="10"/><path d="M8 12l3 3 5-6"/></svg><div><h4>Punctual, uniformed professional chauffeurs</h4><p>Our experienced chauffeurs arrive on time in pristine uniforms with white gloves</p></div></li>
        <li><svg width="15" height="15" viewBox="0 0 24 24" fill="none" stroke="#f7d774" stroke-width="2" stroke-linecap="round"><circle cx="12" cy="12" r="10"/><path d="M8 12l3 3 5-6"/></svg><div><h4>Exceptional comfort, safety, and style</h4><p>Fully insured, regularly maintained vehicles ensuring the highest standards</p></div></li>
        <li><svg width="15" height="15" viewBox="0 0 24 24" fill="none" stroke="#f7d774" stroke-width="2" stroke-linecap="round"><circle cx="12" cy="12" r="10"/><path d="M8 12l3 3 5-6"/></svg><div><h4>Available across Poland for weddings &amp; photo sessions</h4><p>Serving couples throughout Poland with flexible scheduling and locations</p></div></li>
      </ul>
      <div class="details-photo-wrap">
        <div class="details-glow" aria-hidden="true"></div>
        <div class="details-photo" role="img" aria-label="Bride and groom beside a vintage champagne-coloured car"></div>
      </div>
    </div>
  </div>
</section>

<section class="reviews">
  <div class="container">
    <h2 class="section-title">Words from Our <span style="color:var(--gold-soft)">Happy Couples</span></h2>
    <div class="quotes">
      <div class="quote">
        <div class="stars"><svg width="64" height="12" viewBox="0 0 64 12" fill="#f7d774"><g id="s"><path d="M6 0l1.8 3.8 4.2.5-3.1 2.8.8 4.1L6 9.2 2.3 11.2l.8-4.1L0 4.3l4.2-.5z"/></g><use href="#s" x="13"/><use href="#s" x="26"/><use href="#s" x="39"/><use href="#s" x="52"/></svg></div>
        <blockquote>"It felt like a dream. The car was stunning and the service was flawless."</blockquote>
        <cite>– Anna &amp; Michał</cite>
      </div>
      <div class="quote">
        <div class="stars"><svg width="64" height="12" viewBox="0 0 64 12" fill="#f7d774"><use href="#s"/><use href="#s" x="13"/><use href="#s" x="26"/><use href="#s" x="39"/><use href="#s" x="52"/></svg></div>
        <blockquote>"Our guests were amazed. The car made our entrance unforgettable."</blockquote>
        <cite>– Karolina &amp; Patryk</cite>
      </div>
      <div class="quote">
        <div class="stars"><svg width="64" height="12" viewBox="0 0 64 12" fill="#f7d774"><use href="#s"/><use href="#s" x="13"/><use href="#s" x="26"/><use href="#s" x="39"/><use href="#s" x="52"/></svg></div>
        <blockquote>"From start to finish, everything was elegant, smooth, and stress-free."</blockquote>
        <cite>– Marta &amp; Kamil</cite>
      </div>
    </div>
  </div>
</section>

<section class="cta">
  <div class="cta-photo" role="img" aria-label="Wedding couple touching foreheads beside an open car, soft green background"></div>
  <div class="cta-content">
    <h2>Your Dream Car Is <span style="color:var(--gold-soft)">One Click Away</span></h2>
    <p>Reserve early to guarantee availability for your special day.</p>
    <a class="btn btn-gold" href="#contact">Contact Us Today</a>
    <div class="cta-rule" aria-hidden="true"><span></span><i></i><span></span></div>
  </div>
</section>

<footer class="footer" id="contact">
  <div class="container">
    <div class="footer-top">
      <div class="footer-brand">
        <div class="logo"><span>WestaKolory.pl</span><span class="logo-dot"></span></div>
        <p>Creating unforgettable wedding moments with luxury vehicles and professional service. Your special day deserves nothing less than perfection.</p>
        <div class="socials" aria-label="Social media"><span></span><span></span></div>
      </div>
      <div class="footer-col">
        <h5>Quick Links</h5>
        <ul><li>Home</li><li>Fleet</li><li>Services</li><li>Why Us</li><li>Contact</li><li>FAQ</li></ul>
      </div>
      <div class="footer-col">
        <h5>Contact</h5>
        <ul>
          <li><svg width="10" height="10" viewBox="0 0 24 24" fill="none" stroke="#f7d774" stroke-width="2"><rect x="2" y="5" width="20" height="14" rx="2"/><path d="M2 7l10 6 10-6"/></svg>hello@veloraweddingrides.pl</li>
          <li><svg width="10" height="10" viewBox="0 0 24 24" fill="none" stroke="#f7d774" stroke-width="2"><path d="M5 3h4l2 5-3 2a12 12 0 0 0 6 6l2-3 5 2v4a2 2 0 0 1-2 2A18 18 0 0 1 3 5a2 2 0 0 1 2-2z"/></svg>+48 501 220 874</li>
          <li><svg width="10" height="10" viewBox="0 0 24 24" fill="none" stroke="#f7d774" stroke-width="2"><circle cx="12" cy="12" r="10"/><path d="M12 6v6l4 2"/></svg>Mon-Sun: 8:00-20:00</li>
        </ul>
      </div>
    </div>
    <div class="footer-bottom"><span>© 2024 Velora Wedding Rides. All rights reserved.</span><span>English</span></div>
  </div>
</footer>

</body>
</html>
```